Vantiqo custom business card design

Need a authentic, innovative business card design for a new mobile app business. I am uploading a few screen images from our app for you to view. I would like app design theme to match business card design. I can also send logo images.

```html
<!DOCTYPE html>
<html lang="en">
<head>
<meta charset="utf-8">
<title>Vantiqo Business Card</title>
<link href="https://fonts.googleapis.com/css2?family=Work+Sans:wght@400;500;800&display=swap" rel="stylesheet">
<style>
  :root {
    --stage: #9a9a9a;
    --card-dark: #1f1f1f;
    --card-light: #ffffff;
    --brand-purple: #6a2f9a;
    --text-light: #ffffff;
    --text-dark: #1c1c1c;
  }
  * { margin: 0; padding: 0; box-sizing: border-box; }
  html, body { width: 1200px; height: 930px; overflow: hidden; }
  body {
    background: var(--stage);
    font-family: "Work Sans", Arial, sans-serif;
    position: relative;
  }
  .card {
    position: absolute;
    left: 280px;
    width: 640px;
    height: 366px;
    border-radius: 22px;
    overflow: hidden;
    background: var(--card-dark);
    box-shadow: 0 10px 24px rgba(0,0,0,0.35);
  }
  .card--front { top: 69px; }
  .card--back { top: 495px; }

  .brand {
    display: flex;
    flex-direction: column;
    align-items: center;
    gap: 14px;
  }
  .brand__dot {
    width: 92px;
    height: 92px;
    border-radius: 50%;
    background: var(--brand-purple);
  }
  .brand__name {
    font-weight: 800;
    font-size: 46px;
    letter-spacing: 0.5px;
    line-height: 1;
  }
  .card--front .brand {
    position: absolute;
    left: 50%;
    top: 50%;
    transform: translate(-50%, -50%);
  }
  .card--front .brand__name { color: var(--text-light); }

  .back-art { position: absolute; inset: 0; }
  .card--back .brand {
    position: absolute;
    right: 56px;
    top: 40px;
  }
  .card--back .brand__name { color: var(--text-dark); }

  .contact {
    position: absolute;
    left: 44px;
    bottom: 34px;
    color: var(--text-light);
  }
  .contact__name {
    font-weight: 500;
    font-size: 22px;
    letter-spacing: 0.5px;
    text-transform: uppercase;
  }
  .contact__role {
    font-size: 15px;
    margin-bottom: 14px;
  }
  .contact__address {
    font-size: 15px;
    line-height: 1.3;
    margin-bottom: 14px;
  }
  .contact__list { list-style: none; font-size: 15px; line-height: 1.45; }
  .contact__list li { display: flex; align-items: center; gap: 10px; }
  .contact__list svg { width: 13px; height: 13px; flex: none; }
</style>
</head>
<body>

<section class="card card--front" aria-label="Card front">
  <div class="brand">
    <span class="brand__dot"></span>
    <span class="brand__name">Vantiqo</span>
  </div>
</section>

<section class="card card--back" aria-label="Card back">
  <svg class="back-art" viewBox="0 0 640 366" preserveAspectRatio="none" aria-hidden="true">
    <path d="M200,0 Q300,300 640,268 L640,0 Z" fill="var(--card-light)"/>
    <path d="M192,0 Q292,300 640,268" fill="none" stroke="var(--brand-purple)" stroke-width="6"/>
  </svg>

  <div class="brand">
    <span class="brand__dot"></span>
    <span class="brand__name">Vantiqo</span>
  </div>

  <div class="contact">
    <p class="contact__name">Daniel Reyes</p>
    <p class="contact__role">Director</p>
    <p class="contact__address">2750 Harbor Lane<br>Coral Bay, FL 32071</p>
    <ul class="contact__list">
      <li>
        <svg viewBox="0 0 12 12"><rect x="3" y="0.5" width="6" height="11" rx="1" fill="none" stroke="#fff" stroke-width="1.2"/></svg>
        (555) 410-2281
      </li>
      <li>
        <svg viewBox="0 0 12 12"><path d="M2,1 L4.5,1 L5.5,3.5 L4,4.5 Q5,7 7.5,8 L8.5,6.5 L11,7.5 L11,10 Q6,11 2,6 Q1,3 2,1 Z" fill="#fff"/></svg>
        (555) 410-7734
      </li>
      <li>
        <svg viewBox="0 0 12 12"><rect x="0.6" y="2" width="10.8" height="8" fill="none" stroke="#fff" stroke-width="1.2"/><path d="M0.6,2 L6,6.5 L11.4,2" fill="none" stroke="#fff" stroke-width="1.2"/></svg>
        info@Vantiqo.com
      </li>
      <li>
        <svg viewBox="0 0 12 12"><circle cx="6" cy="6" r="5.2" fill="none" stroke="#fff" stroke-width="1.1"/><ellipse cx="6" cy="6" rx="2.2" ry="5.2" fill="none" stroke="#fff" stroke-width="1"/><line x1="0.8" y1="6" x2="11.2" y2="6" stroke="#fff" stroke-width="1"/></svg>
        www.Vantiqo.com
      </li>
    </ul>
  </div>
</section>

</body>
</html>
```